Keystone Trench Co Business Card*

Looking for a professional, clean and crisp business card

I am in the underground utilities industry and am just looking for a really impressive business card. I would like our card to be white with our symbol crisp and clear with it protruding. I also have a business partner that will require his name and info on the card once the design is set. I would like to have our website info on the card which is;
http://keystonetrenchco.example/

Contact Information for Business Card

Website, contact name, number and email

```html
<!DOCTYPE html>
<html lang="en">
<head>
<meta charset="utf-8">
<title>Keystone Trench Co — Business Card</title>
<link rel="stylesheet" href="https://fonts.googleapis.com/css2?family=Oswald:wght@500&family=Roboto+Condensed:wght@400&display=swap">
<style>
  :root {
    --backdrop: #b4b4b4;
    --brand-blue: #3862a9;
    --brand-blue-deep: #2f5799;
    --card-white: #ffffff;
    --ink: #1c1c1c;
    --rule: #333333;
  }
  * { margin: 0; padding: 0; box-sizing: border-box; }
  html, body {
    width: 1200px; height: 1200px; overflow: hidden;
    background: var(--backdrop);
  }
  .stage { position: relative; width: 1200px; height: 1200px; }
  .card {
    position: absolute; top: 303px; width: 369px; height: 594px;
    box-shadow: 3px 3px 4px rgba(0,0,0,0.45);
  }
  .card--front {
    left: 201px;
    background: linear-gradient(160deg, var(--brand-blue) 0%, var(--brand-blue) 55%, var(--brand-blue-deep) 100%);
    color: var(--card-white);
  }
  .card--back { left: 599px; width: 365px; background: var(--card-white); color: var(--ink); }

  .wordmark {
    position: absolute; left: 0; right: 0;
    text-align: center;
    font-family: "Oswald", sans-serif; font-weight: 500;
    text-transform: uppercase; line-height: 1.02;
  }
  .card--front .wordmark { top: 232px; font-size: 46px; color: var(--card-white); }
  .card--back .wordmark { top: 140px; font-size: 44px; color: var(--ink); }
  .wordmark__dot {
    display: block; width: 14px; height: 14px; margin: 0 auto 12px;
    border-radius: 50%; background: currentColor;
  }

  .front-web {
    position: absolute; left: 0; right: 0; top: 535px;
    text-align: center;
    font-family: "Roboto Condensed", sans-serif; font-size: 17px; letter-spacing: 1.6px;
  }

  .contact { position: absolute; left: 0; right: 0; top: 386px; text-align: center; }
  .contact__name {
    font-family: "Oswald", sans-serif; font-weight: 500;
    font-size: 27px; line-height: 1; color: var(--brand-blue);
    text-transform: uppercase; transform: scaleX(0.85);
  }
  .contact__role {
    font-family: "Roboto Condensed", sans-serif; font-size: 17px; margin-top: 4px;
  }
  .contact__icons {
    display: flex; align-items: center; justify-content: center; gap: 5px;
    margin-top: 13px;
  }
  .contact__rule { width: 33px; height: 1px; background: var(--rule); margin: 0 4px; }
  .icon {
    width: 25px; height: 25px; border-radius: 3px; background: var(--brand-blue);
    display: flex; align-items: center; justify-content: center;
  }
  .contact__lines {
    margin-top: 12px;
    font-family: "Roboto Condensed", sans-serif; font-size: 18px; line-height: 24.5px;
  }
</style>
</head>
<body>
<main class="stage">
  <section class="card card--front">
    <div class="wordmark">
      <span class="wordmark__dot"></span>
      Keystone<br>Trench Co
    </div>
    <p class="front-web">www.keystonetrenchco.example</p>
  </section>

  <section class="card card--back">
    <div class="wordmark">
      <span class="wordmark__dot"></span>
      Keystone<br>Trench Co
    </div>
    <div class="contact">
      <h1 class="contact__name">Daniel Mercer</h1>
      <p class="contact__role">Managing Director</p>
      <div class="contact__icons">
        <span class="contact__rule"></span>
        <span class="icon" aria-label="Phone">
          <svg width="15" height="15" viewBox="0 0 16 16"><path d="M2 6c0-2 3-3 6-3s6 1 6 3v1h-3V5.5H5V7H2z M4 8h8l1 5H3z" fill="#fff"/></svg>
        </span>
        <span class="icon" aria-label="Email">
          <svg width="16" height="12" viewBox="0 0 16 12"><rect x="0.75" y="0.75" width="14.5" height="10.5" fill="none" stroke="#fff" stroke-width="1.2"/><path d="M1 1l7 6 7-6M1 11l5-5M15 11l-5-5" fill="none" stroke="#fff" stroke-width="1"/></svg>
        </span>
        <span class="icon" aria-label="Website">
          <svg width="16" height="16" viewBox="0 0 16 16"><circle cx="8" cy="8" r="7" fill="#fff"/><path d="M4 4c2 0 3 1 2 3s1 3 0 5M10 3c0 2 2 2 3 4" fill="none" stroke="#3862a9" stroke-width="1.6"/></svg>
        </span>
        <span class="contact__rule"></span>
      </div>
      <p class="contact__lines">
        044-555 010 203<br>
        info@keystonetrench.example<br>
        www.keystonetrenchco.example
      </p>
    </div>
  </section>
</main>
</body>
</html>
```